New Business Card Design Project

Use the flyer uploaded and website www.brightoakbuilders.com for inspiration.
List Our Services on Backside of business cards
Marcus Delling
Harborline Builders Inc.
Licensed General Contractors
858-471-6093

Contact Information for Business Card

Use the flyer uploaded and website www.brightoakbuilders.com for inspiration. List Our Services on Backside of business cards Marcus Delling Harborline Builders Inc. Licensed General Contractors 858-471-6093

```html
<!DOCTYPE html>
<html lang="en">
<head>
<meta charset="utf-8">
<title>Harborline Builders – Business Cards</title>
<link href="https://fonts.googleapis.com/css2?family=Montserrat:wght@400;500;700;800&display=swap" rel="stylesheet">
<style>
  :root {
    --stage: #2b2b2b;
    --card-dark: #1e1e1e;
    --card-white: #f7f8f7;
    --ink-light: #f2f2f2;
    --ink-muted: #bdbdbd;
    --ink-dark: #111111;
    --rule: #8a8a8a;
  }
  * { margin: 0; padding: 0; box-sizing: border-box; }
  html, body {
    width: 1200px; height: 875px; overflow: hidden;
    background: var(--stage);
    font-family: "Montserrat", sans-serif;
  }
  .stage {
    position: relative; width: 1200px; height: 875px;
  }
  .card {
    position: absolute; left: 265px;
    width: 670px; height: 383px;
    border-radius: 22px;
    background: var(--card-dark);
    color: var(--ink-light);
    overflow: hidden;
    box-shadow: 0 14px 30px rgba(0,0,0,.45);
  }
  .card--back { top: 40px; }
  .card--front { top: 452px; }

  .brand {
    display: flex; align-items: center; justify-content: center; gap: 14px;
  }
  .brand__mark {
    width: 14px; height: 14px; border: 1.5px solid var(--ink-light);
  }
  .brand__name {
    font-weight: 500; font-size: 30px; letter-spacing: 3px;
    text-transform: uppercase; color: var(--ink-light);
  }

  /* back */
  .card--back .brand { margin-top: 70px; }
  .services__title {
    margin: 34px auto 0; width: max-content;
    font-weight: 800; font-size: 20px;
    padding-bottom: 6px; border-bottom: 1.5px solid var(--ink-light);
  }
  .services__list {
    list-style: none; margin-top: 36px;
    display: flex; flex-direction: column; align-items: center; gap: 14px;
    font-size: 13.5px; font-weight: 400;
  }
  .services__row { display: flex; gap: 20px; }
  .services__row span::before { content: "•"; margin-right: 6px; }

  /* front */
  .card--front .brand { position: absolute; top: 92px; left: 0; right: 0; }
  .info-band {
    position: absolute; left: 0; right: 0; top: 212px; height: 118px;
    background: var(--card-white); color: var(--ink-dark);
    display: flex; align-items: center; justify-content: center; gap: 26px;
  }
  .person { text-align: right; }
  .person__name { font-weight: 800; font-size: 26px; }
  .person__role { font-size: 13px; margin-top: 2px; }
  .divider { width: 1px; height: 72px; background: var(--ink-dark); }
  .contacts { list-style: none; display: flex; flex-direction: column; gap: 9px; font-size: 14px; }
  .contacts li { display: flex; align-items: center; gap: 10px; }
  .contacts svg { width: 14px; height: 14px; fill: var(--ink-dark); }
  .license {
    position: absolute; left: 0; right: 0; top: 348px;
    text-align: center; font-size: 13px; color: var(--ink-muted);
  }
</style>
</head>
<body>
<main class="stage">

  <section class="card card--back" aria-label="Business card back">
    <div class="brand">
      <span class="brand__mark"></span>
      <span class="brand__name">Harborline Builders</span>
    </div>
    <h2 class="services__title">Our Services</h2>
    <ul class="services__list">
      <li class="services__row"><span>Remodel: Kitchen &amp; Bath</span><span>Painting: Interior &amp; Exterior</span><span>Flooring: Carpet, Vinyl, Wood</span></li>
      <li class="services__row"><span>Window: Door Replacement</span><span>Plumbing: Repair &amp; Upgrades</span><span>Energy Efficient Upgrades</span></li>
      <li class="services__row"><span>Deck &amp; Patio construction</span><span>Water &amp; Mold Damage</span><span>Garage Renovation</span></li>
    </ul>
  </section>

  <section class="card card--front" aria-label="Business card front">
    <div class="brand">
      <span class="brand__mark"></span>
      <span class="brand__name">Harborline Builders</span>
    </div>
    <div class="info-band">
      <div class="person">
        <p class="person__name">Marcus Delling</p>
        <p class="person__role">Managing Director</p>
      </div>
      <span class="divider"></span>
      <ul class="contacts">
        <li><svg viewBox="0 0 16 16"><path d="M3 1h3l1.5 4-2 1.2a9 9 0 0 0 4.3 4.3L11 8.5l4 1.5v3a2 2 0 0 1-2 2A12 12 0 0 1 1 3a2 2 0 0 1 2-2z"/></svg>858-471-6093</li>
        <li><svg viewBox="0 0 16 16"><path d="M1 3h14v10H1z M1 3l7 6 7-6" fill="none" stroke="#111" stroke-width="1.6"/></svg>info@brightoakbuilders.com</li>
        <li><svg viewBox="0 0 16 16"><circle cx="8" cy="8" r="6.5" fill="none" stroke="#111" stroke-width="1.5"/><path d="M1.5 8h13M8 1.5c-3 3-3 10 0 13M8 1.5c3 3 3 10 0 13" fill="none" stroke="#111" stroke-width="1.2"/></svg>www.brightoakbuilders.com</li>
      </ul>
    </div>
    <p class="license">CSLB Licensed No. #1048265</p>
  </section>

</main>
</body>
</html>
```